Web Design Project

The aim of this project to design a website for a service that would offer services for small business and non profit organizations using opensource software that is weaved to work together in harmony.

The website name is: vestolia.net

Vestolia in Arabic means: cabbage. Cabbage is composed of leaves, actually there is nothing except leaves. Each leave by itself is not called cabbage, but a collection of leaves that are organized in a central way would give us cabbage.

Same idea for Vestolia where open source software very well organized and integrated would create a new thing with a new value.

Target Market(s)

Small business, Europe, Africa, Far east and Middle east

Industry/Entity Type

Small Business

Requirements
Must have
• The website would offer the following sections:
* Home page
* Benefits: value of vestolia
* Applications: applications offered by vestolia
* Pricing
* Purchase
* Customer log in
* Support
- FAQ
- Knowledge base
- Forums
- Open tickets

Please take the following consideration in design:
* White should predominate
* Only black and the colors of logo are permitted (attched)
Nice to have
• Design is better to express:
* Openness
* Dynamic
* Usable
* Cost effective

```html
<!DOCTYPE html>
<html lang="en">
<head>
<meta charset="utf-8">
<title>vestolia – Creating a new thing with a new value</title>
<link rel="stylesheet" href="https://fonts.googleapis.com/css2?family=Questrial&family=Mulish:wght@700&family=Oswald:wght@500&family=Open+Sans:wght@400;600;700&display=swap">
<style>
  :root {
    --green: #8cc63f;
    --green-dark: #6fa92a;
    --blue: #0095da;
    --yellow: #f7c100;
    --magenta: #b54e8e;
    --ink: #222222;
    --text: #555555;
    --heading-grey: #7a7068;
    --rule: #c9c1b8;
    --field-bg: #f4f4f4;
    --field-border: #cfcfcf;
    --footer-bg: #666666;
    --hero-top: #6e9a36;
    --hero-bottom: #dfe9cf;
    --white: #ffffff;
  }
  * { box-sizing: border-box; margin: 0; padding: 0; }
  html, body { width: 1040px; height: 1200px; overflow: hidden; background: var(--white); }
  body { position: relative; font-family: "Open Sans", Arial, sans-serif; color: var(--text); }

  /* Header */
  .brand { position: absolute; left: 20px; top: 38px; display: flex; align-items: center; gap: 12px; }
  .brand-mark { width: 34px; height: 34px; border-radius: 50%; background: var(--green); }
  .brand-name { font-family: "Questrial", Arial, sans-serif; font-size: 40px; color: var(--ink); letter-spacing: -0.5px; }
  .utility { position: absolute; right: 30px; top: 16px; display: flex; gap: 12px; }
  .utility a { display: flex; flex-direction: column; align-items: center; font-family: Arial, sans-serif; font-size: 13px; color: var(--ink); text-decoration: none; gap: 3px; }
  .utility svg { width: 18px; height: 16px; }
  .tagline { position: absolute; right: 28px; top: 68px; font-family: "Questrial", Arial, sans-serif; font-size: 28px; color: var(--ink); }

  /* Navigation */
  .main-nav { position: absolute; left: 0; top: 118px; width: 1040px; height: 30px; background: var(--green); display: flex; }
  .main-nav a { font-family: "Mulish", Arial, sans-serif; font-weight: 700; font-size: 17px; color: var(--white); text-decoration: none; line-height: 30px; text-align: center; }
  .main-nav a.active { background: var(--blue); }

  /* Hero */
  .hero { position: absolute; left: 0; top: 148px; width: 1040px; height: 376px;
    background: linear-gradient(180deg, var(--hero-top) 0%, #9cc764 50%, var(--hero-bottom) 100%); }

  /* Feature cards */
  .feature { position: absolute; top: 573px; width: 319px; height: 190px; color: var(--white); padding: 24px 14px 0; border-top: 4px solid rgba(255,255,255,0.25); overflow: hidden; }
  .feature--support { left: 17px; background: var(--yellow); }
  .feature--apps { left: 360px; background: var(--blue); }
  .feature--knowledge { left: 699px; background: var(--magenta); }
  .feature-deco { position: absolute; right: 14px; top: 10px; width: 80px; height: 80px; border-radius: 50%; border: 8px solid rgba(255,255,255,0.16); }
  .feature h2 { position: relative; font-family: "Oswald", Arial, sans-serif; font-weight: 500; font-size: 27px; line-height: 32px; text-transform: uppercase; letter-spacing: -0.3px; }
  .feature p { position: relative; font-size: 12.5px; line-height: 15.5px; margin-top: 6px; }
  .read-more { position: absolute; left: 13px; bottom: 24px; width: 100px; height: 26px; border-radius: 13px; background: linear-gradient(#ffffff, #e4e4e4); border: 2px solid #d6d6d6; font-family: "Open Sans", Arial, sans-serif; font-weight: 700; font-size: 10px; color: #6b6b6b; text-align: center; line-height: 22px; text-transform: uppercase; }

  /* Lower columns */
  .column { position: absolute; top: 824px; width: 323px; }
  .column--contact { left: 13px; }
  .column--news { left: 357px; }
  .column--testimonials { left: 698px; }
  .column-stripe { height: 6px; background: repeating-linear-gradient(-45deg, var(--rule) 0 2px, transparent 2px 5px); }
  .column-head { display: flex; align-items: center; gap: 20px; height: 52px; border-bottom: 1px solid var(--rule); }
  .column-head svg { width: 30px; height: 32px; flex: none; }
  .column-head h3 { font-family: "Questrial", Arial, sans-serif; font-weight: 400; font-size: 26px; color: var(--heading-grey); letter-spacing: 0.5px; }

  .contact-form { margin-top: 30px; width: 296px; }
  .field { display: block; width: 100%; height: 30px; margin-bottom: 6px; border: 1px solid var(--field-border); border-radius: 6px; background: var(--field-bg); font-size: 13px; color: #444; padding: 6px 12px; }
  .field--message { height: 72px; }
  .send { display: block; margin-top: 12px; width: 76px; height: 26px; border-radius: 13px; background: linear-gradient(var(--green), var(--green-dark)); border: 2px solid #b7dd8a; color: var(--white); font-weight: 700; font-size: 10px; text-align: center; line-height: 22px; }

  .news-item { display: flex; gap: 15px; margin-top: 30px; }
  .news-item + .news-item { margin-top: 36px; }
  .news-thumb { width: 70px; height: 70px; flex: none; border: 1px solid #d8d8d8; padding: 4px; }
  .news-thumb span { display: block; width: 100%; height: 100%; }
  .thumb-green { background: linear-gradient(135deg, #e4eedb, #8fc04c); }
  .thumb-blue { background: linear-gradient(135deg, #d6f1fb, #3da7d6); }
  .news-date { font-weight: 700; font-size: 14.5px; color: var(--blue); margin-bottom: 4px; }
  .news-item p { font-size: 12.5px; line-height: 15px; }

  .testimonial { position: relative; margin-top: 30px; padding-left: 34px; font-size: 12.5px; line-height: 15.5px; }
  .testimonial::before { content: "\201C"; position: absolute; left: 2px; top: -10px; font-family: Georgia, serif; font-size: 90px; line-height: 1; color: #e1e7f0; }
  .testimonial p { position: relative; margin-bottom: 15px; }
  .testimonial cite { position: relative; font-style: normal; font-weight: 700; color: var(--blue); }

  /* Footer */
  .site-footer { position: absolute; left: 0; top: 1151px; width: 1040px; height: 27px; background: var(--footer-bg); color: var(--white); font-size: 11.5px; line-height: 27px; text-align: center; }
  .site-footer .links { margin-left: 30px; }
</style>
</head>
<body>
  <header>
    <div class="brand"><span class="brand-mark"></span><span class="brand-name">vestolia</span></div>
    <nav class="utility">
      <a href="#"><svg viewBox="0 0 18 16"><rect x="3" y="3" width="12" height="8" fill="#333"/><rect x="1" y="12" width="16" height="2" fill="#333"/></svg>login</a>
      <a href="#"><svg viewBox="0 0 18 16"><circle cx="9" cy="5" r="4" fill="#333"/><path d="M2 16 Q9 6 16 16Z" fill="#333"/></svg>support</a>
      <a href="#"><svg viewBox="0 0 18 16"><text x="9" y="13" text-anchor="middle" font-family="Arial" font-weight="700" font-size="13" fill="#333">?</text></svg>FAQ</a>
    </nav>
    <p class="tagline">Creating a new thing with a new value</p>
  </header>

  <nav class="main-nav">
    <a class="active" href="#" style="width:127px">home</a>
    <a href="#" style="width:112px">benefits</a>
    <a href="#" style="width:130px">applications</a>
    <a href="#" style="width:105px">pricing</a>
    <a href="#" style="width:120px">purchase</a>
    <a href="#" style="width:175px">knowledge base</a>
    <a href="#" style="width:135px">open tickets</a>
  </nav>

  <div class="hero" role="img" aria-label="Hero photo: hands on a tablet beneath a glowing green globe with floating data panels"></div>

  <section class="feature feature--support">
    <span class="feature-deco"></span>
    <h2>24/7 Client Support</h2>
    <p>Lorem ipsum dolor sit amet, consectetuer adipiscing elit, sed diam nonummy nibh euismod tincidunt ut laoreet dolore magna.</p>
    <span class="read-more">Read more</span>
  </section>
  <section class="feature feature--apps">
    <span class="feature-deco"></span>
    <h2>Applications</h2>
    <p>Duis autem vel eum iriure dolor in hendrerit in vulputate velit esse molestie consequat, vel illum dolore eu feugiat nulla facilisis at vero eros.</p>
    <span class="read-more">Read more</span>
  </section>
  <section class="feature feature--knowledge">
    <span class="feature-deco"></span>
    <h2>Knowledge Base</h2>
    <p>Ut wisi enim ad minim veniam, quis nostrud exerci tation ullamcorper suscipit lobortis nisl ut aliquip ex ea commodo consequat.</p>
    <span class="read-more">Read more</span>
  </section>

  <section class="column column--contact">
    <div class="column-stripe"></div>
    <div class="column-head">
      <svg viewBox="0 0 30 32"><circle cx="15" cy="11" r="7" fill="#7a7068"/><path d="M2 32 Q2 19 15 19 Q28 19 28 32Z" fill="#7a7068"/><path d="M7 11 Q7 2 15 2 Q23 2 23 11" stroke="#8cc63f" stroke-width="2.5" fill="none"/></svg>
      <h3>CONTACT US</h3>
    </div>
    <div class="contact-form">
      <span class="field">Full Name</span>
      <span class="field">Email Address</span>
      <span class="field field--message">Message</span>
      <span class="send">SEND</span>
    </div>
  </section>

  <section class="column column--news">
    <div class="column-stripe"></div>
    <div class="column-head">
      <svg viewBox="0 0 30 32"><rect x="3" y="6" width="24" height="22" rx="2" fill="none" stroke="#7a7068" stroke-width="2.5"/><rect x="3" y="6" width="24" height="6" fill="#7a7068"/><rect x="8" y="2" width="3" height="7" fill="#7a7068"/><rect x="19" y="2" width="3" height="7" fill="#7a7068"/><text x="15" y="25" text-anchor="middle" font-family="Arial" font-weight="700" font-size="10" fill="#7a7068">15</text></svg>
      <h3>LATEST NEWS</h3>
    </div>
    <div class="news-item">
      <div class="news-thumb"><span class="thumb-green" role="img" aria-label="Green arrow icon"></span></div>
      <div><p class="news-date">Fri, January. 03</p><p>Lorem ipsum dolor sit amet, consectet adipiscing elit, sed diam nonummy nibh euismod tincidunt ut .</p></div>
    </div>
    <div class="news-item">
      <div class="news-thumb"><span class="thumb-blue" role="img" aria-label="Blue globe icon"></span></div>
      <div><p class="news-date">Mon, December. 28</p><p>Lorem ipsum dolor sit amet, consectet adipiscing elit, sed diam nonummy nibh euismod tincidunt ut .</p></div>
    </div>
  </section>

  <section class="column column--testimonials">
    <div class="column-stripe"></div>
    <div class="column-head">
      <svg viewBox="0 0 30 32"><ellipse cx="14" cy="14" rx="12" ry="9" fill="#7a7068"/><path d="M7 20 L5 27 L13 22Z" fill="#7a7068"/></svg>
      <h3>TESTIMONIALS</h3>
    </div>
    <blockquote class="testimonial">
      <p>Duis autem vel eum iriure dolor in hendrerit in vulputate velit esse molestie consequat, vel illum dolore eu feugiat nulla facilisis at vero eros et accumsan et iusto odio.</p>
      <p>Nam liber tempor cum soluta nobis eleifend option congue nihil imperdiet doming id quod mazim placerat facer possim assum.</p>
      <cite>mr. Tomas Realo (manager)</cite>
    </blockquote>
  </section>

  <footer class="site-footer">Copyright 2014. All rights reserved.<span class="links">Privacy Policy | Terms of Use</span></footer>
</body>
</html>
```